Private lender of mortgages and rent to own housing

need a website that reflects real estate especially mortgage lending and rent to own houses..
Sections as follows
Home About Types of mortgages Rent to own Contact us
Target Market(s)
consumers who require non traditonal mortgages
Industry/Entity Type
Mortgage
Coding
Coded - Design and coding required
Number of Pages Required
4 page
Font styles to use
Sans Serif
Colors
Designer to choose colors to be used in the design.
Requirements
Must have
- background pictures on pages. with nice picture on homepage of houses or a community
Nice to have
- contact us form i supplied a ink to

```html
<!DOCTYPE html>
<html lang="en">
<head>
<meta charset="utf-8">
<title>Maplecrest Lending Group</title>
<link href="https://fonts.googleapis.com/css2?family=Open+Sans:wght@400;600;700;800&display=swap" rel="stylesheet">
<style>
:root{
  --navy:#29286b;
  --navy-deep:#1f1e55;
  --violet:#3c3a8e;
  --ink:#1d1d1d;
  --muted:#8a8a8a;
  --line:#e4e4e4;
  --white:#ffffff;
  --band:#2c3036;
}
*{box-sizing:border-box;margin:0;padding:0}
html,body{width:1200px;height:3237px;overflow:hidden}
body{position:relative;background:var(--white);font-family:"Open Sans",Arial,sans-serif;color:var(--ink)}
.abs{position:absolute}
.btn{position:absolute;background:var(--navy);color:var(--white);font-weight:600;text-transform:uppercase;display:flex;align-items:center;justify-content:center;letter-spacing:.3px}

/* header */
.brand{left:97px;top:66px;font-size:15px;font-weight:700;color:var(--navy);letter-spacing:.3px}
.brand-mark{left:160px;top:20px;width:44px;height:40px;border:3px solid var(--navy);border-radius:50%}
.quote-btn{left:978px;top:32px;width:122px;height:39px;font-size:12px}
.main-nav{left:276px;top:101px;width:648px;height:50px;background:var(--white);box-shadow:0 2px 10px rgba(0,0,0,.15);display:flex;align-items:center;justify-content:space-around;padding:0 24px;font-size:12.5px;text-transform:uppercase;color:#333;z-index:2}
.main-nav .active{color:var(--navy);font-weight:600}

/* hero */
.hero{left:0;top:134px;width:1200px;height:520px;background:linear-gradient(120deg,#4a6a8f 0%,#9fb2c6 35%,#c9cfd6 55%,#8a6a5a 80%,#b23a2c 100%)}
.hero-shade{left:0;top:134px;width:1200px;height:520px;background:rgba(20,25,40,.28)}
.hero-title{left:0;top:288px;width:1200px;text-align:center;color:var(--white);font-size:42px;font-weight:700}
.hero-sub{left:0;top:360px;width:1200px;text-align:center;color:var(--white);font-size:21px;font-weight:700;line-height:33px}
.hero-btn{left:466px;top:447px;width:268px;height:53px;font-size:16px;font-weight:700}
.dots{left:574px;top:612px;display:flex;gap:4px}
.dots span{width:11px;height:11px;border-radius:50%;border:2px solid var(--white)}
.dots span:first-child{background:var(--white)}

/* about */
.about-title{left:97px;top:722px;font-size:26px;font-weight:700}
.about-tag{left:97px;top:760px;font-size:14px;font-weight:700}
.about-copy{left:97px;top:795px;width:308px;font-size:11.5px;line-height:21px;color:var(--muted)}
.about-copy p+p{margin-top:14px}
.about-btn{left:97px;top:1045px;width:95px;height:35px;font-size:11px}
.gallery{border:1px solid #ccc}
.g1{left:427px;top:727px;width:335px;height:376px;background:linear-gradient(135deg,#c7cfd6,#e9ecef 50%,#7e8a94)}
.g2{left:768px;top:727px;width:397px;height:184px;background:linear-gradient(135deg,#dfe5ea,#9aa9b7)}
.g3{left:768px;top:917px;width:397px;height:186px;background:linear-gradient(135deg,#c7b7a6,#8e8c8a 60%,#cfd4d9)}

/* features band */
.features{left:0;top:1178px;width:1200px;height:311px;background:linear-gradient(90deg,#2b2f36,#4b3d33 50%,#22262c)}
.feature{position:absolute;top:1250px;width:320px;text-align:center;color:var(--white)}
.feature svg{display:block;margin:0 auto 26px}
.feature h3{font-size:17px;font-weight:400;margin-bottom:12px}
.feature p{font-size:11.5px;line-height:22px}

/* services */
.section-title{left:0;width:1200px;text-align:center;font-size:24px;font-weight:700}
.service{position:absolute;top:1624px;width:260px;text-align:center}
.ring{width:148px;height:148px;margin:0 auto;border-radius:50%;border:3px solid #d6d6d6;display:flex;align-items:center;justify-content:center}
.ring-inner{width:116px;height:116px;border-radius:50%;border:2px solid #bbb;display:flex;align-items:center;justify-content:center}
.service h3{margin-top:34px;font-size:16px;font-weight:700;text-transform:uppercase}
.service p{margin:12px auto 0;width:210px;font-size:11.5px;line-height:24px;color:var(--muted)}
.service .more{margin:12px auto 0;width:98px;height:28px;background:var(--navy);color:var(--white);font-size:11px;font-weight:600;display:flex;align-items:center;justify-content:center}

/* testimonial */
.testimonial{left:0;top:2007px;width:1200px;height:363px;background:linear-gradient(90deg,var(--violet),#4a4a9a 50%,#2f2e78)}
.avatar{left:99px;top:2085px;width:202px;height:202px;border-radius:50%;border:6px solid var(--white);background:linear-gradient(160deg,#d9d9de,#6a6a78)}
.quote{left:421px;top:2066px;width:670px;color:var(--white);font-size:11.5px;line-height:27px}
.quote b{font-size:22px;font-family:Georgia,serif;vertical-align:-4px;margin-right:6px}
.author{left:426px;top:2202px;color:var(--white);font-size:11px;text-transform:uppercase}
.stars{left:424px;top:2230px}

/* help */
.help-sub{left:0;top:2487px;width:1200px;text-align:center;font-size:18px;font-weight:700}
.card{top:2536px;height:295px;display:flex;align-items:center;justify-content:center;color:var(--white);font-weight:700;text-shadow:0 1px 4px rgba(0,0,0,.5)}
.c1{left:97px;width:317px;background:linear-gradient(180deg,#e8ebee,#b9b1a3);font-size:20px}
.c2{left:440px;width:315px;background:linear-gradient(180deg,#2f5d86,#3b6f98);font-size:24px;box-shadow:0 6px 12px rgba(0,0,0,.25)}
.c3{left:783px;width:317px;background:linear-gradient(180deg,#dfe6ec,#b8c3cc);font-size:20px}
.arrow{top:2646px;width:74px;height:74px;border-radius:50%;background:var(--white);box-shadow:0 1px 6px rgba(0,0,0,.2);display:flex;align-items:center;justify-content:center}

/* footer */
.foot-col{position:absolute;top:2940px}
.foot-col h4{font-size:14px;font-weight:700;margin-bottom:18px}
.foot-col li{list-style:none;font-size:11.5px;color:#666;line-height:30px}
.news{display:flex;gap:14px;margin-bottom:18px}
.news .thumb{width:66px;height:50px;background:linear-gradient(135deg,#c8b08a,#8e7a5a)}
.news .t{font-size:11.5px;color:#666;line-height:19px;width:150px}
.news .meta{font-size:11px;color:#777;margin-top:4px}
.social{display:flex;gap:14px}
.social span{width:22px;height:22px;border-radius:50%;background:var(--navy)}
.copyright{left:0;top:3172px;width:1200px;border-top:1px solid var(--line);padding-top:10px;text-align:center;font-size:11px;color:#888}
</style>
</head>
<body>

<header>
  <div class="abs brand-mark" aria-hidden="true"></div>
  <div class="abs brand">MAPLECREST LENDING GROUP</div>
  <div class="btn quote-btn">Get a Quote</div>
  <nav class="abs main-nav">
    <span class="active">Home</span><span>About</span><span>Types of Mortgages</span><span>Rent to Own</span><span>Contact Us</span>
    <svg width="14" height="14" viewBox="0 0 14 14"><circle cx="6" cy="6" r="4.2" fill="none" stroke="var(--navy)" stroke-width="2"/><line x1="9" y1="9" x2="13" y2="13" stroke="var(--navy)" stroke-width="2"/></svg>
  </nav>
</header>

<section>
  <div class="abs hero" role="img" aria-label="Handshake over a desk with a model house, mortgage papers and a pen"></div>
  <div class="abs hero-shade"></div>
  <h1 class="abs hero-title">We are leading Financial Provider for Houses</h1>
  <p class="abs hero-sub">Save yourself thousands of dollars in interest, lower your monthly payments<br>and get debt free faster by consolidating your debts</p>
  <div class="btn hero-btn">Read More Information</div>
  <div class="abs dots"><span></span><span></span><span></span><span></span></div>
</section>

<section>
  <h2 class="abs about-title">About</h2>
  <div class="abs about-tag">We Can Put You in Your Own Home Today</div>
  <div class="abs about-copy">
    <p>We know life sometimes delivers challenges and it can be hard to get back on track once you have dealt with challenges. Maybe you have been through a divorce, bankruptcy, consumer proposal, loss of job, work place injury, new to the country, self employed. None of these things has to bind you to a lifetime of renting.</p>
    <p>We focus on rent to own in Pine Ridge County and our Renting Program is a very viable option for those that can't get a mortgage today but are willing to work towards getting approved in the near future.</p>
  </div>
  <div class="btn about-btn">Read More</div>
  <div class="abs gallery g1" role="img" aria-label="Model houses with a calculator and growth chart"></div>
  <div class="abs gallery g2" role="img" aria-label="Mortgage application form with a calculator"></div>
  <div class="abs gallery g3" role="img" aria-label="Couple meeting with a mortgage advisor"></div>
</section>

<section>
  <div class="abs features" role="img" aria-label="Hands joined together in teamwork"></div>
  <div class="feature" style="left:69px">
    <svg width="56" height="50" viewBox="0 0 56 50" fill="#fff"><circle cx="28" cy="12" r="9"/><circle cx="11" cy="17" r="6"/><circle cx="45" cy="17" r="6"/><path d="M14 48c0-12 6-20 14-20s14 8 14 20z"/><path d="M0 44c0-9 4-15 11-15 3 0 5 1 6 2-3 4-5 8-5 13z"/><path d="M56 44c0-9-4-15-11-15-3 0-5 1-6 2 3 4 5 8 5 13z"/></svg>
    <h3>Dedicated Team</h3>
    <p>Lacus leo tristique ornare tellus sed suscipit porta<br>risus fusce molestie...</p>
  </div>
  <div class="feature" style="left:440px">
    <svg width="50" height="50" viewBox="0 0 50 50" fill="none" stroke="#fff" stroke-width="6" stroke-linecap="round"><rect x="4" y="4" width="20" height="14" rx="7" transform="rotate(45 14 11)"/><rect x="26" y="32" width="20" height="14" rx="7" transform="rotate(45 36 39)"/><line x1="20" y1="20" x2="30" y2="30"/></svg>
    <h3>Secure Process</h3>
    <p>Lacus leo tristique ornare tellus sed suscipit porta<br>risus fusce molestie...</p>
  </div>
  <div class="feature" style="left:768px">
    <svg width="50" height="50" viewBox="0 0 50 50" fill="none" stroke="#fff" stroke-width="5"><path d="M7 32V25a18 18 0 0 1 36 0v7"/><rect x="4" y="28" width="10" height="16" rx="3" fill="#fff"/><rect x="36" y="28" width="10" height="16" rx="3" fill="#fff"/></svg>
    <h3>24/ 7 Support</h3>
    <p>Lacus leo tristique ornare tellus sed suscipit porta<br>risus fusce molestie...</p>
  </div>
</section>

<section>
  <h2 class="abs section-title" style="top:1552px">OUR SERVICES</h2>
  <div class="service" style="left:69px">
    <div class="ring"><div class="ring-inner"><svg width="46" height="46" viewBox="0 0 46 46" fill="none" stroke="var(--navy)"><circle cx="23" cy="23" r="18" stroke-width="7"/><circle cx="23" cy="23" r="8" stroke-width="3"/></svg></div></div>
    <h3>Down Payment</h3><p>Lorem Ipsum is simply dummy text of the printing and typesetting</p><div class="more">READ MORE</div>
  </div>
  <div class="service" style="left:336px">
    <div class="ring"><div class="ring-inner"><svg width="48" height="34" viewBox="0 0 48 34"><rect x="2" y="2" width="44" height="30" fill="none" stroke="var(--navy)" stroke-width="4"/><rect x="8" y="8" width="32" height="18" fill="var(--navy)"/><circle cx="24" cy="17" r="6" fill="#fff"/></svg></div></div>
    <h3>Household Income</h3><p>Lorem Ipsum is simply dummy text of the printing and typesetting</p><div class="more">READ MORE</div>
  </div>
  <div class="service" style="left:604px">
    <div class="ring"><div class="ring-inner"><svg width="36" height="46" viewBox="0 0 36 46" fill="none" stroke="var(--navy)" stroke-width="3"><path d="M3 3h20l10 10v30H3z"/><path d="M23 3v10h10"/><line x1="9" y1="22" x2="27" y2="22"/><line x1="9" y1="29" x2="27" y2="29"/><line x1="9" y1="36" x2="27" y2="36"/></svg></div></div>
    <h3>Credit Report</h3><p>Lorem Ipsum is simply dummy text of the printing and typesetting</p><div class="more">READ MORE</div>
  </div>
  <div class="service" style="left:869px">
    <div class="ring"><div class="ring-inner"><svg width="44" height="40" viewBox="0 0 44 40" fill="var(--navy)"><path d="M22 2 2 20h6v18h11V27h6v11h11V20h6z"/></svg></div></div>
    <h3>Selecting a House</h3><p>Lorem Ipsum is simply dummy text of the printing and typesetting</p><div class="more">READ MORE</div>
  </div>
</section>

<section>
  <div class="abs testimonial" role="img" aria-label="Blue tinted background of a house exterior"></div>
  <div class="abs avatar" role="img" aria-label="Portrait of a client in a business suit"></div>
  <p class="abs quote"><b>&ldquo;</b>Aliquam dictum elit vitae mauris facilisis, at dictum urna dignissim. Donec vel lectus vel felis lacinia luctus vitae tow iaculis arcu. Mauris mattis, massa eu porta ultricies. Aliquam dictum elit vitae metus lobortis sed facilisis, augue pellentesque nunc tempus ornare quam lorem dictum urna dignissim. <b>&rdquo;</b></p>
  <div class="abs author">Daniel Morrow</div>
  <svg class="abs stars" width="84" height="16" viewBox="0 0 84 16" fill="#fff">
    <path id="star" d="M8 0l2.4 5 5.6.6-4.2 3.8 1.2 5.6L8 12.2 3 15l1.2-5.6L0 5.6 5.6 5z"/>
    <use href="#star" x="17"/><use href="#star" x="34"/><use href="#star" x="51"/>
    <path d="M76 0l2.4 5 5.6.6-4.2 3.8 1.2 5.6L76 12.2z" opacity=".5"/><path d="M76 0v12.2L71 15l1.2-5.6L68 5.6l5.6-.6z"/>
  </svg>
</section>

<section>
  <h2 class="abs section-title" style="top:2437px">WE ARE HERE TO HELP YOU</h2>
  <div class="abs help-sub">Rent to Own a House</div>
  <div class="abs card c1" role="img" aria-label="Hourglass with gears">Debut Consolidation</div>
  <div class="abs card c2" role="img" aria-label="Business people above a banknote">Bridge Financing</div>
  <div class="abs card c3" role="img" aria-label="Figure climbing a rising red arrow chart">Equity Take Out</div>
  <div class="abs arrow" style="left:58px"><svg width="20" height="34" viewBox="0 0 20 34"><path d="M17 2 3 17l14 15" fill="none" stroke="#999" stroke-width="2"/></svg></div>
  <div class="abs arrow" style="left:1063px"><svg width="20" height="34" viewBox="0 0 20 34"><path d="M3 2l14 15L3 32" fill="none" stroke="#999" stroke-width="2"/></svg></div>
</section>

<footer>
  <div class="foot-col" style="left:97px"><h4>Quick Links</h4><ul><li>Home</li><li>About</li><li>Types of Mortgages</li><li>Rent to own</li><li>Contact Us</li></ul></div>
  <div class="foot-col" style="left:330px"><h4>Useful Links</h4><ul><li>Guides</li><li>Make An Appointment</li><li>Call Us</li><li>&#9993;&nbsp; info@maplecrestlending.ca</li></ul></div>
  <div class="foot-col" style="left:591px"><h4>Latest News</h4>
    <div class="news"><div class="thumb" role="img" aria-label="Small house model"></div><div><div class="t">Welcome to Our Lending News Blog</div><div class="meta">&#9635; Sep 6, 2017 &nbsp;&nbsp; &#9650; 4</div></div></div>
    <div class="news"><div class="thumb" role="img" aria-label="House keys on a table" style="background:linear-gradient(135deg,#d5d8dc,#9aa2aa)"></div><div><div class="t">Welcome to Our Lending News Blog</div><div class="meta">&#9635; Sep 6, 2017 &nbsp;&nbsp; &#9650; 4</div></div></div>
  </div>
  <div class="foot-col" style="left:926px"><h4>Contact Us On</h4><div class="social"><span></span><span></span><span></span><span></span><span></span></div></div>
  <div class="abs copyright">&copy; 2017 Maplecrest Lending. All Rights Reserved.</div>
</footer>

</body>
</html>
```